Request for Business Card Design

Hi. My name is Marlene, I am looking for a new business card design for my company, Quarrow Signal Instruments, LLC. I really like the design you did for Tarsel Venture and was hoping you could do something similar using our full logo and our mark. I am also open to any raised texture design using our mark. I have attached our full logo, which would need to be somewhere on the card, as well as the mark in both outline and full form, as well as our brand colors / guide. The card does not have to be white, as long as our logo and mark appear. I actually like darker colored business cards more, but am open to all options. If you are interested in working with me, please let me know. We would also take the business card design into letterhead design if you can do that.

```html
<!DOCTYPE html>
<html lang="en">
<head>
<meta charset="utf-8">
<title>Quarrow Signal Instruments — Business Card</title>
<link rel="stylesheet" href="https://fonts.googleapis.com/css2?family=Montserrat:wght@800&family=Arimo:ital,wght@0,400;1,400&display=swap">
<style>
  :root {
    --stage: #121212;
    --card: #222223;
    --card-deep: #1c1c1d;
    --brand-blue: #0a8bb3;
    --ink: #ffffff;
    --ink-soft: #e6e6e6;
  }
  * { box-sizing: border-box; margin: 0; padding: 0; }
  html, body { width: 1200px; height: 963px; overflow: hidden; }
  body {
    background: var(--stage);
    display: flex;
    flex-direction: column;
    align-items: center;
    justify-content: center;
    gap: 40px;
    font-family: "Arimo", Arial, sans-serif;
  }
  .card {
    position: relative;
    width: 720px;
    height: 411px;
    border-radius: 26px;
    background: var(--card);
    box-shadow: 0 0 0 3px var(--brand-blue), 0 20px 40px rgba(0,0,0,.6);
    overflow: hidden;
  }
  .wordmark {
    position: absolute;
    display: flex;
    align-items: center;
    gap: 18px;
  }
  .wordmark-dot {
    width: 58px; height: 58px;
    border-radius: 50%;
    background: var(--brand-blue);
    flex: none;
  }
  .wordmark-name {
    font-family: "Montserrat", Arial, sans-serif;
    font-weight: 800;
    color: var(--ink);
    font-size: 34px;
    line-height: 1.02;
    letter-spacing: 2px;
    text-transform: uppercase;
  }
  .front .wordmark { top: 64px; left: 190px; }

  .person {
    position: absolute;
    top: 200px; right: 400px;
    text-align: right;
  }
  .person-name {
    font-family: "Montserrat", Arial, sans-serif;
    font-weight: 800;
    color: var(--brand-blue);
    font-size: 24px;
    letter-spacing: 1px;
    text-transform: uppercase;
  }
  .person-role {
    color: var(--ink-soft);
    font-style: italic;
    font-size: 18px;
    margin-top: 4px;
  }
  .divider {
    position: absolute;
    top: 196px; left: 345px;
    width: 1px; height: 96px;
    background: var(--ink-soft);
  }
  .contacts {
    position: absolute;
    top: 200px; left: 368px;
    list-style: none;
    display: flex; flex-direction: column; gap: 10px;
  }
  .contacts li {
    display: flex; align-items: center; gap: 12px;
    color: var(--ink); font-size: 18px;
  }
  .contacts svg { width: 18px; height: 18px; flex: none; }
  .address {
    position: absolute;
    top: 330px; left: 0; right: 0;
    text-align: center;
    color: var(--ink); font-size: 18px;
  }

  .back-texture {
    position: absolute; inset: 0;
    background: radial-gradient(circle at 40% 40%, #262627 0%, var(--card) 55%, var(--card-deep) 100%);
  }
  .back .wordmark { top: 168px; left: 160px; }
</style>
</head>
<body>

<section class="card front" aria-label="Business card front">
  <div class="wordmark">
    <span class="wordmark-dot"></span>
    <span class="wordmark-name">Quarrow<br>Signal Instruments</span>
  </div>

  <div class="person">
    <p class="person-name">Dorian Vale</p>
    <p class="person-role">Manager</p>
  </div>

  <span class="divider"></span>

  <ul class="contacts">
    <li>
      <svg viewBox="0 0 24 24" fill="none" stroke="var(--brand-blue)" stroke-width="2" stroke-linecap="round" stroke-linejoin="round"><path d="M22 16.9v3a2 2 0 0 1-2.2 2 19.8 19.8 0 0 1-8.6-3.1 19.5 19.5 0 0 1-6-6A19.8 19.8 0 0 1 2.1 4.2 2 2 0 0 1 4.1 2h3a2 2 0 0 1 2 1.7c.1 1 .4 1.9.7 2.8a2 2 0 0 1-.5 2.1L8 9.9a16 16 0 0 0 6 6l1.3-1.3a2 2 0 0 1 2.1-.4c.9.3 1.8.6 2.8.7a2 2 0 0 1 1.7 2z"/></svg>
      555-014-2100
    </li>
    <li>
      <svg viewBox="0 0 24 24" fill="none" stroke="var(--brand-blue)" stroke-width="2" stroke-linejoin="round"><rect x="2" y="5" width="20" height="14" rx="1"/><path d="M2 6l10 7 10-7"/></svg>
      hello@quarrowsignal.com
    </li>
    <li>
      <svg viewBox="0 0 24 24" fill="none" stroke="var(--brand-blue)" stroke-width="2"><circle cx="12" cy="12" r="10"/><path d="M2 12h20M12 2a15 15 0 0 1 0 20M12 2a15 15 0 0 0 0 20"/></svg>
      www.quarrowsignal.com
    </li>
  </ul>

  <p class="address">18 Ferrow Lane, Aldmere, CO 80112</p>
</section>

<section class="card back" aria-label="Business card back">
  <div class="back-texture" role="img" aria-label="Raised texture pattern of the brand mark across the card"></div>
  <div class="wordmark">
    <span class="wordmark-dot"></span>
    <span class="wordmark-name">Quarrow<br>Signal Instruments</span>
  </div>
</section>

</body>
</html>
```